Business Card Design

We need a business card designed for our new company. Prefer a black card with white logo & writing.

Contact Information for Business Card

Ted Galloway, address: 7-4812 Fernhollow Road, Abbotsford, BC, V3K 8R2, Office Phone: 604-712-3390, Cell: 604-947-2164, Email: ted@resinworkshub.ca

Colors

Designer to choose only greyscale colors for use in the design.

```html
<!DOCTYPE html>
<html lang="en">
<head>
<meta charset="utf-8">
<title>Resin Works Hub — Business Card</title>
<link href="https://fonts.googleapis.com/css2?family=Poppins:wght@300;400;600;800&display=swap" rel="stylesheet">
<style>
  :root {
    --backdrop: #2b2b2c;
    --card: #1d1d1f;
    --white: #ffffff;
    --soft-white: #e9e9e9;
    --grey-light: #4a4a4d;
    --grey-mid: #353537;
    --tab: #f3f1ea;
  }
  * { margin: 0; padding: 0; box-sizing: border-box; }
  html, body { width: 1200px; height: 780px; overflow: hidden; }
  body {
    background: var(--backdrop);
    font-family: "Poppins", sans-serif;
    color: var(--white);
    position: relative;
  }
  .card {
    position: absolute;
    top: 240px;
    width: 525px;
    height: 300px;
    background: var(--card);
    box-shadow: 0 14px 30px rgba(0,0,0,0.45);
    overflow: hidden;
  }
  .card--front { left: 50px; }
  .card--back { left: 625px; }

  .wordmark {
    display: flex;
    align-items: center;
    gap: 10px;
    font-weight: 800;
    letter-spacing: 0.5px;
    line-height: 1;
    text-transform: uppercase;
  }
  .wordmark__square {
    background: var(--white);
    flex: none;
  }
  .card--front .wordmark {
    position: absolute;
    left: 34px;
    top: 34px;
    font-size: 22px;
  }
  .card--front .wordmark__square { width: 16px; height: 16px; }

  .contact-list {
    position: absolute;
    left: 34px;
    top: 112px;
    list-style: none;
    font-size: 12px;
    font-weight: 300;
    line-height: 1.55;
  }
  .contact-list li { display: flex; align-items: center; gap: 9px; }
  .contact-list svg { width: 11px; height: 11px; flex: none; }

  .layered-accent {
    position: absolute;
    left: 250px;
    top: 140px;
    width: 150px;
    height: 140px;
    background: linear-gradient(160deg, var(--grey-light), var(--grey-mid) 60%, var(--card));
    clip-path: polygon(50% 0, 100% 45%, 55% 100%, 0 55%);
  }

  .person {
    position: absolute;
    right: 44px;
    top: 96px;
    text-align: right;
  }
  .person__name {
    font-size: 30px;
    line-height: 1.1;
    font-weight: 300;
  }
  .person__name strong { font-weight: 600; }
  .person__title {
    font-size: 13px;
    font-weight: 300;
    margin-top: 2px;
  }
  .name-tab {
    position: absolute;
    right: 0;
    top: 100px;
    width: 24px;
    height: 56px;
    background: var(--tab);
  }

  .address {
    position: absolute;
    right: 44px;
    bottom: 28px;
    text-align: right;
    font-size: 13px;
    font-weight: 300;
    line-height: 1.5;
  }

  .card--back .wordmark {
    position: absolute;
    inset: 0;
    justify-content: center;
    font-size: 36px;
    gap: 14px;
  }
  .card--back .wordmark__square { width: 26px; height: 26px; }
</style>
</head>
<body>
  <section class="card card--front" aria-label="Business card, contact side">
    <div class="wordmark"><span class="wordmark__square"></span>Resin Works Hub</div>

    <ul class="contact-list">
      <li>
        <svg viewBox="0 0 24 24" fill="#fff" aria-hidden="true"><path d="M6.6 10.8a15 15 0 0 0 6.6 6.6l2.2-2.2a1 1 0 0 1 1-.25 11.4 11.4 0 0 0 3.6.57 1 1 0 0 1 1 1V20a1 1 0 0 1-1 1A17 17 0 0 1 3 4a1 1 0 0 1 1-1h3.5a1 1 0 0 1 1 1c0 1.25.2 2.45.57 3.57a1 1 0 0 1-.25 1z"/></svg>
        604-712-3390
      </li>
      <li>
        <svg viewBox="0 0 24 24" fill="none" stroke="#fff" stroke-width="2" aria-hidden="true"><rect x="6" y="2" width="12" height="20" rx="2"/><line x1="11" y1="18" x2="13" y2="18"/></svg>
        604-947-2164
      </li>
      <li>
        <svg viewBox="0 0 24 24" fill="none" stroke="#fff" stroke-width="2" aria-hidden="true"><circle cx="12" cy="12" r="10"/><line x1="2" y1="12" x2="22" y2="12"/><path d="M12 2a15 15 0 0 1 0 20a15 15 0 0 1 0-20"/></svg>
        www.resinworkshub.ca
      </li>
      <li>
        <svg viewBox="0 0 24 24" fill="none" stroke="#fff" stroke-width="2" aria-hidden="true"><rect x="2" y="5" width="20" height="14" rx="1"/><polyline points="2,6 12,13 22,6"/></svg>
        ted@resinworkshub.ca
      </li>
    </ul>

    <div class="layered-accent" role="img" aria-label="Decorative layered grey shape"></div>

    <div class="name-tab"></div>
    <div class="person">
      <p class="person__name"><strong>Ted</strong> Galloway</p>
      <p class="person__title">Founder &amp; CEO</p>
    </div>

    <address class="address" style="font-style: normal;">
      7-4812 Fernhollow Road,<br>
      Abbotsford, BC, V3K 8R2.
    </address>
  </section>

  <section class="card card--back" aria-label="Business card, brand side">
    <div class="wordmark"><span class="wordmark__square"></span>Resin Works Hub</div>
  </section>
</body>
</html>
```